Biz Cards to match new logo

I'm looking for a business card layout to go with my new logo. I'd like to have one side in colour (purple, with the logo in white) and the other side to be white with the purple logo and contact info in black font: name, address (2 lines), phone, email, fax, website. The logo includes the company name so it doesn't need to be repeated in the text. The font should be legibile to the semi-blind. (I hate small fonts on business cards).

Industry/Entity Type

Business

```html
<!DOCTYPE html>
<html lang="en">
<head>
<meta charset="UTF-8">
<title>Quillmere Research – Business Card</title>
<link rel="stylesheet" href="https://fonts.googleapis.com/css2?family=Lato:wght@400;700;900&display=swap">
<style>
  :root {
    --purple: #6a4289;
    --ink: #111111;
    --paper: #ffffff;
    --stage: #2b2b2b;
    --black-band: #000000;
  }
  * { box-sizing: border-box; margin: 0; padding: 0; }
  html, body {
    width: 1200px;
    height: 926px;
    overflow: hidden;
    background: var(--stage);
    font-family: "Lato", Arial, sans-serif;
  }
  .sheet {
    width: 1200px;
    height: 926px;
    display: flex;
    flex-direction: column;
    align-items: center;
    justify-content: center;
    gap: 56px;
  }
  .card {
    position: relative;
    width: 640px;
    height: 366px;
    overflow: hidden;
  }

  /* Back side */
  .card--back {
    background: var(--purple);
    display: flex;
    align-items: center;
    justify-content: center;
  }
  .wordmark {
    display: flex;
    flex-direction: column;
    align-items: center;
    font-weight: 900;
    letter-spacing: 0.08em;
    text-transform: uppercase;
    line-height: 1;
  }
  .wordmark__name { font-size: 44px; }
  .wordmark__sub { font-size: 17px; letter-spacing: 0.42em; margin-top: 8px; }
  .card--back .wordmark { color: var(--paper); }

  /* Front side */
  .card--front { background: var(--paper); }
  .holder {
    position: absolute;
    left: 40px;
    top: 32px;
  }
  .holder__name {
    font-size: 27px;
    font-weight: 400;
    color: var(--purple);
    line-height: 1.1;
  }
  .holder__name strong { font-weight: 900; }
  .holder__title {
    font-size: 13px;
    font-weight: 700;
    color: var(--ink);
    margin-top: 2px;
  }
  .contacts {
    position: absolute;
    left: 40px;
    top: 128px;
    list-style: none;
  }
  .contacts li {
    display: flex;
    align-items: center;
    gap: 10px;
    font-size: 18px;
    color: var(--ink);
    line-height: 24px;
  }
  .contacts svg { width: 14px; height: 14px; fill: var(--purple); flex: none; }
  .address {
    position: absolute;
    left: 40px;
    top: 240px;
    font-size: 18px;
    line-height: 25px;
    color: var(--ink);
    font-style: normal;
  }
  .card--front .wordmark {
    position: absolute;
    right: 36px;
    top: 226px;
    color: var(--purple);
  }
  .card--front .wordmark__name { font-size: 34px; }
  .card--front .wordmark__sub { font-size: 14px; margin-top: 6px; }
  .band {
    position: absolute;
    bottom: 0;
    height: 46px;
  }
  .band--black { left: 0; width: 57%; background: var(--black-band); }
  .band--purple { right: 0; width: 43%; background: var(--purple); }
</style>
</head>
<body>
<main class="sheet">
  <section class="card card--back" aria-label="Card back">
    <div class="wordmark">
      <span class="wordmark__name">Quillmere</span>
      <span class="wordmark__sub">Research</span>
    </div>
  </section>

  <section class="card card--front" aria-label="Card front">
    <div class="holder">
      <h1 class="holder__name">Dana <strong>Whitlow</strong></h1>
      <p class="holder__title">title goes here</p>
    </div>

    <ul class="contacts">
      <li>
        <svg viewBox="0 0 16 16" aria-hidden="true"><path d="M2 5c0-2 2-3 6-3s6 1 6 3v1h-3V5H5v1H2zM4 7h8l2 6H2z"/></svg>
        555-201-4478
      </li>
      <li>
        <svg viewBox="0 0 16 16" aria-hidden="true"><path d="M4 1h8v4H4zM1 6h14v6h-3v3H4v-3H1zM5 10v4h6v-4z"/></svg>
        555-201-4479
      </li>
      <li>
        <svg viewBox="0 0 16 16" aria-hidden="true"><path d="M1 3h14v1L8 9 1 4zM1 6l7 5 7-5v7H1z"/></svg>
        dana@quillmere.example
      </li>
      <li>
        <svg viewBox="0 0 16 16" aria-hidden="true"><path d="M6 10l4-4 1 1-4 4zM3 9l2-2 1 1-2 2 2 2 2-2 1 1-2 2c-1 1-2 1-3 0l-1-1c-1-1-1-2 0-3zM10 3c1-1 2-1 3 0l1 1c1 1 1 2 0 3l-2 2-1-1 2-2-2-2-2 2-1-1z"/></svg>
        www.quillmere.example
      </li>
    </ul>

    <address class="address">
      48 Larkspur Lane,<br>
      Suite #210, Fenwick Bldg, NY 10457
    </address>

    <div class="wordmark">
      <span class="wordmark__name">Quillmere</span>
      <span class="wordmark__sub">Research</span>
    </div>

    <div class="band band--black"></div>
    <div class="band band--purple"></div>
  </section>
</main>
</body>
</html>
```